Camp Thornbriar Day Camp Brochure

I need someone to design a brochure for our day camp. It will be 8.5 x 11 inch paper folded horizontally. Looking for a fun, clean design. I sent several pictures, not all of them have to be used. The brochure will be mailed out to former day campers and used at events to help us market our program. A colorful brochure would be nice. I would like the cover page to be portrait along with the two inside pages. The back cover will need to be landscape format.

Target Market(s)

Parents

Colors

Designer to choose colors to be used in the design.

Requirements
Must have
• All information provided. Great design on the inside pages

```html
<!DOCTYPE html>
<html lang="en">
<head>
<meta charset="utf-8">
<title>Camp Thornbriar Day Camp 2019 Brochure</title>
<link href="https://fonts.googleapis.com/css2?family=Lato:wght@400;700;900&family=Oswald:wght@500;700&display=swap" rel="stylesheet">
<style>
  :root{
    --green:#2fb53f;
    --green-deep:#1f9a2f;
    --charcoal:#444546;
    --ink:#3a3a3a;
    --mist:#ececec;
    --paper:#ffffff;
    --stage:#eceaea;
    --photo-a:#5f7a3e;
    --photo-b:#b9a27d;
    --photo-c:#2e4a26;
  }
  *{box-sizing:border-box;margin:0;padding:0}
  html,body{width:1200px;height:2647px;overflow:hidden;background:var(--stage)}
  body{font-family:'Lato',sans-serif;color:var(--ink);position:relative}
  .spread{position:absolute;left:60px;width:1080px;height:840px;display:flex;box-shadow:0 18px 40px rgba(0,0,0,.12)}
  .spread--outside{top:300px}
  .spread--inside{top:1500px}
  .page{position:relative;width:540px;height:840px;overflow:hidden;background:var(--paper)}
  .page__art{position:absolute;inset:0;width:100%;height:100%}
  .photo{position:absolute;background:linear-gradient(135deg,var(--photo-a),var(--photo-b) 55%,var(--photo-c))}
  .photo--round{border-radius:50%;border:8px solid var(--paper);box-shadow:0 4px 14px rgba(0,0,0,.25)}

  /* cover */
  .cover__title{position:absolute;right:40px;top:58px;text-align:right;line-height:1.05}
  .cover__camp{color:var(--green);font-size:26px}
  .cover__name{font-size:28px;color:var(--charcoal)}
  .cover__dc{font-size:30px;font-weight:700;color:var(--charcoal)}
  .cover__dc span{color:var(--green)}
  .cover__rule{position:absolute;right:40px;top:178px;width:210px;height:3px;background:var(--charcoal)}
  .cover__intro{position:absolute;right:40px;top:196px;width:270px;font-size:10px;line-height:1.45;color:#666}

  /* mailer back (rotated landscape panel) */
  .mailer{position:absolute;left:0;top:0;width:840px;height:540px;transform-origin:0 0;transform:translate(0,840px) rotate(-90deg)}
  .mailer__return{position:absolute;left:600px;top:40px;font-size:10px;line-height:1.5;color:#666}
  .mailer__stamp{position:absolute;right:40px;top:36px;width:70px;height:80px;border:2px solid var(--charcoal)}
  .mailer__lines{position:absolute;left:490px;top:150px;width:290px}
  .mailer__lines span{display:block;height:2px;background:#9a9a9a;margin-bottom:30px}
  .mailer__org{position:absolute;left:260px;top:120px;width:215px}
  .mailer__org h2{font-size:17px;font-weight:900;color:var(--green);line-height:1.2}
  .contact{list-style:none;margin-top:10px;font-size:10.5px;color:#555}
  .contact li{display:flex;align-items:center;gap:8px;margin-bottom:5px;white-space:nowrap}
  .contact svg{width:12px;height:12px;fill:var(--green);flex:none}

  /* inside left */
  .info{position:absolute;left:345px;width:175px}
  .info h3{font-family:'Oswald',sans-serif;color:var(--green);font-size:17px;letter-spacing:.5px;line-height:1.2}
  .info p{font-size:10px;line-height:1.5;color:#555;margin-top:6px}
  .price{display:flex;align-items:center;gap:10px;margin-top:10px}
  .price__amt{font-family:'Oswald',sans-serif;font-size:30px;color:var(--charcoal)}
  .price__amt small{font-size:18px;color:var(--green)}
  .price__note{font-size:10px;line-height:1.3;color:var(--green);font-weight:700}
  .since{position:absolute;left:222px;top:268px;width:110px;height:110px;border-radius:50%;background:var(--paper);border:4px solid var(--green);display:flex;flex-direction:column;align-items:center;justify-content:center;font-family:'Oswald',sans-serif;color:var(--green);line-height:1}
  .since b{font-size:26px}
  .since span{font-size:13px}
  .facts{position:absolute;left:345px;top:570px;width:175px;list-style:none}
  .facts li{display:flex;gap:8px;margin-bottom:14px;font-size:10px;line-height:1.35;color:#555}
  .facts .dot{flex:none;width:22px;height:22px;border-radius:50%;border:2px solid var(--green);display:flex;align-items:center;justify-content:center}
  .facts .dot svg{width:10px;height:10px;fill:var(--green)}
  .facts b{display:block;color:var(--green);font-size:11px}

  /* inside right */
  .hours{position:absolute;left:40px;top:60px;width:250px;list-style:none}
  .hours li{margin-bottom:14px;padding-left:18px;position:relative;font-size:10px;color:#666}
  .hours li::before{content:"";position:absolute;left:0;top:4px;width:8px;height:8px;border-radius:50%;background:var(--green)}
  .hours b{display:block;font-size:13px;color:var(--green);font-weight:900}
  .details{position:absolute;left:40px;top:310px;width:260px;font-size:10px;line-height:1.5;color:#555}
  .details h4{color:var(--green);font-size:12px;margin-top:10px}
  .register{position:absolute;left:40px;top:500px;width:290px;font-family:'Oswald',sans-serif;line-height:1.1}
  .register h2{font-size:30px;color:var(--charcoal)}
  .register p{font-size:18px;color:var(--green)}
  .register small{display:block;font-family:'Lato',sans-serif;font-size:10px;color:#666;margin-top:4px}
  .dates{position:absolute;left:322px;top:670px;width:195px;color:var(--paper)}
  .dates h4{font-size:15px;margin-bottom:6px}
  .dates ul{list-style:none;font-size:10.5px;line-height:1.55}
  .dates li{display:flex;justify-content:space-between}
  .dates li b{font-weight:900}
</style>
</head>
<body>

<section class="spread spread--outside">
  <!-- back cover (mailing panel, landscape) -->
  <article class="page page--back">
    <svg class="page__art" viewBox="0 0 540 840" preserveAspectRatio="none" aria-hidden="true">
      <rect width="540" height="840" fill="var(--mist)"/>
      <path d="M540 0 Q420 0 400 60 L540 60Z" fill="var(--charcoal)"/>
      <path d="M0 700 Q280 740 540 640 L540 840 L0 840Z" fill="var(--charcoal)"/>
      <path d="M200 840 Q380 800 540 700 L540 840Z" fill="var(--green)"/>
      <path d="M0 720 Q260 780 540 690" fill="none" stroke="var(--paper)" stroke-width="4"/>
    </svg>
    <div class="mailer">
      <div class="mailer__return">Camp Thornbriar<br>418 Briarwood Lane<br>Maple Hollow, OH 45000</div>
      <div class="mailer__stamp"></div>
      <div class="mailer__lines"><span></span><span></span><span></span><span></span></div>
      <div class="mailer__org">
        <h2>Camp Thornbriar<br>Christian Summer Camp</h2>
        <ul class="contact">
          <li><svg viewBox="0 0 24 24"><path d="M12 2a7 7 0 0 0-7 7c0 5 7 13 7 13s7-8 7-13a7 7 0 0 0-7-7zm0 9.5A2.5 2.5 0 1 1 12 6a2.5 2.5 0 0 1 0 5.5z"/></svg>418 Briarwood Lane, Maple Hollow</li>
          <li><svg viewBox="0 0 24 24"><path d="M6.6 10.8a15 15 0 0 0 6.6 6.6l2.2-2.2a1 1 0 0 1 1-.25 11.4 11.4 0 0 0 3.6.57 1 1 0 0 1 1 1V20a1 1 0 0 1-1 1A17 17 0 0 1 3 4a1 1 0 0 1 1-1h3.5a1 1 0 0 1 1 1 11.4 11.4 0 0 0 .57 3.6 1 1 0 0 1-.25 1z"/></svg>(555) 014-2278</li>
          <li><svg viewBox="0 0 24 24"><circle cx="12" cy="12" r="10"/></svg>hello@campthornbriar.org</li>
        </ul>
      </div>
    </div>
  </article>

  <!-- front cover -->
  <article class="page page--cover">
    <svg class="page__art" viewBox="0 0 540 840" preserveAspectRatio="none" aria-hidden="true">
      <rect width="540" height="840" fill="var(--mist)"/>
      <path d="M0 0 L110 0 Q0 200 140 400 Q40 520 0 560Z" fill="var(--charcoal)"/>
      <path d="M0 0 L70 0 Q-20 200 90 400 L0 430Z" fill="var(--green)"/>
      <ellipse cx="400" cy="150" rx="260" ry="220" fill="var(--paper)"/>
      <path d="M0 580 Q260 720 540 480 L540 840 L0 840Z" fill="var(--green)"/>
      <path d="M0 640 Q280 760 540 560" fill="none" stroke="var(--green-deep)" stroke-width="14"/>
      <path d="M0 730 Q240 860 540 780 L540 840 L0 840Z" fill="var(--charcoal)"/>
    </svg>
    <div class="cover__title">
      <div class="cover__camp">Camp</div>
      <div class="cover__name">Thornbriar</div>
      <div class="cover__dc">DAY CAMP <span>2019</span></div>
    </div>
    <div class="cover__rule"></div>
    <p class="cover__intro">Thornbriar is special: a place many of us call home. As a non-profit, Thornbriar depends upon donors, former campers, counselors, and family to help keep the mission alive.</p>
    <div class="photo photo--round" style="left:150px;top:350px;width:240px;height:240px" role="img" aria-label="Photo of three young campers standing together outdoors under trees"></div>
  </article>
</section>

<section class="spread spread--inside">
  <!-- inside left -->
  <article class="page page--inside-left">
    <svg class="page__art" viewBox="0 0 540 840" preserveAspectRatio="none" aria-hidden="true">
      <rect width="540" height="840" fill="var(--mist)"/>
    </svg>
    <div class="photo" style="left:0;top:0;width:300px;height:840px;border-radius:0 260px 0 0 / 0 420px 0 0" role="img" aria-label="Photo of campers playing together in a shaded wooded area"></div>
    <svg class="page__art" viewBox="0 0 540 840" preserveAspectRatio="none" aria-hidden="true">
      <path d="M300 0 Q220 180 290 330 Q360 470 280 640 Q230 760 290 840" fill="none" stroke="var(--green)" stroke-width="6"/>
    </svg>
    <div class="photo photo--round" style="left:250px;top:20px;width:150px;height:150px" role="img" aria-label="Photo of a camper on playground equipment"></div>
    <div class="since"><span>SINCE</span><b>1950</b></div>
    <div class="info" style="top:190px">
      <h3>CAMP THORNBRIAR<br>DAY CAMP</h3>
      <p>A week of games, crafts, swimming and friendship in the woods for campers ages 5 to 12.</p>
    </div>
    <div class="info" style="top:410px">
      <div class="price"><span class="price__amt"><small>$</small>105</span><span class="price__note">per week<br>full day program</span></div>
      <div class="price"><span class="price__amt"><small>$</small>120</span><span class="price__note">per week<br>with extended care</span></div>
    </div>
    <ul class="facts">
      <li><span class="dot"><svg viewBox="0 0 24 24"><path d="M9 16.2 4.8 12l-1.4 1.4L9 19 21 7l-1.4-1.4z"/></svg></span><span><b>Ages 5 – 12</b>Grouped by age with caring trained counselors.</span></li>
      <li><span class="dot"><svg viewBox="0 0 24 24"><path d="M9 16.2 4.8 12l-1.4 1.4L9 19 21 7l-1.4-1.4z"/></svg></span><span><b>What to bring</b>Lunch, water bottle, sunscreen and swimsuit.</span></li>
      <li><span class="dot"><svg viewBox="0 0 24 24"><path d="M9 16.2 4.8 12l-1.4 1.4L9 19 21 7l-1.4-1.4z"/></svg></span><span><b>Discounts</b>Save ten percent for each added sibling.</span></li>
    </ul>
  </article>

  <!-- inside right -->
  <article class="page page--inside-right">
    <svg class="page__art" viewBox="0 0 540 840" preserveAspectRatio="none" aria-hidden="true">
      <rect width="540" height="840" fill="var(--paper)"/>
      <path d="M540 560 Q300 560 250 700 Q220 800 260 840 L540 840Z" fill="var(--green)"/>
      <path d="M540 600 Q330 600 285 720 Q265 790 290 840" fill="none" stroke="var(--paper)" stroke-width="4"/>
    </svg>
    <div class="photo" style="left:330px;top:20px;width:210px;height:300px;border-radius:180px 0 0 180px" role="img" aria-label="Photo of a smiling young camper eating a snack outdoors"></div>
    <ul class="hours">
      <li><b>Drop off</b>7:30 AM – 9:00 AM at the main lodge</li>
      <li><b>Camp day</b>9:00 AM – 4:00 PM, Monday to Friday</li>
      <li><b>Pick up</b>4:00 PM – 5:30 PM with extended care</li>
    </ul>
    <div class="details">
      <h4>Activities</h4>
      Swimming, archery, crafts, nature hikes, games and daily chapel time.
      <h4>Registration</h4>
      Spots are limited each week. Register early to hold your camper's place.
    </div>
    <div class="register">
      <h2>REGISTER TODAY</h2>
      <p>AT CAMPTHORNBRIAR.ORG</p>
      <small>or call (555) 014-2278</small>
    </div>
    <div class="photo photo--round" style="left:40px;top:700px;width:120px;height:120px" role="img" aria-label="Photo of a group of campers gathered together"></div>
    <div class="dates">
      <h4>Dates</h4>
      <ul>
        <li><b>WEEK 1</b><span>June 10th – 14th</span></li>
        <li><b>WEEK 2</b><span>June 17th – 21st</span></li>
        <li><b>WEEK 3</b><span>June 24th – 28th</span></li>
        <li><b>WEEK 4</b><span>July 8th – 12th</span></li>
        <li><b>WEEK 5</b><span>July 15th – 19th</span></li>
        <li><b>WEEK 6</b><span>July 29th – August 2nd</span></li>
      </ul>
    </div>
  </article>
</section>

</body>
</html>
```